SirKettle needs a new packaging

We are Coffee Roasters based in Versailles France.

We want a new design for our coffee packaging. The packaging is a basic brown paper bag. We are sticking on it a 99.1mm x 67.7mm Label.

We want a new design for the label. The label should have the following info : Name of the coffee, origin, one line of description, our website www.sirkettle.fr.

Enclosed you will find our logo, as well as a picture of our current packaging

The Design should be "simple yet sophisticate".

```html
<!DOCTYPE html>
<html lang="fr">
<head>
<meta charset="UTF-8">
<title>SirKettle – Étiquette No5</title>
<link rel="stylesheet" href="https://fonts.googleapis.com/css2?family=Josefin+Slab:wght@300;400&family=Open+Sans:wght@400;600&display=swap">
<style>
  :root{
    --ink:#3b2312;
    --ink-soft:#5a3a22;
    --paper:#ffffff;
    --stage:#ffffff;
    --ornament-a:#4a2c16;
    --ornament-b:#7a5234;
    --leaf:#6f8f4a;
    --berry:#b2322a;
  }
  *{margin:0;padding:0;box-sizing:border-box}
  html,body{width:1200px;height:1000px;overflow:hidden;background:var(--stage)}
  .canvas{position:relative;width:1200px;height:1000px}
  .label{
    position:absolute;left:100px;top:158px;width:1000px;height:683px;
    background:var(--paper);
    box-shadow:0 6px 18px rgba(0,0,0,.28);
    color:var(--ink);text-align:center;
    font-family:"Josefin Slab",serif;
  }
  .frame{position:absolute;inset:0}
  .corner{
    position:absolute;width:120px;height:120px;
    background:radial-gradient(circle at 30% 30%,var(--ornament-b),var(--ornament-a) 70%);
    opacity:.85;border-radius:6px;
  }
  .corner.tl{left:22px;top:22px}
  .corner.tr{right:22px;top:22px}
  .corner.bl{left:22px;bottom:22px}
  .corner.br{right:22px;bottom:22px}
  .sprig{
    position:absolute;left:440px;top:18px;width:120px;height:56px;
    background:linear-gradient(90deg,var(--leaf),var(--berry) 50%,var(--leaf));
    border-radius:28px;
  }
  .brand{
    position:absolute;left:0;right:0;top:88px;
    display:flex;align-items:center;justify-content:center;gap:28px;
  }
  .brand-dot{width:110px;height:110px;border-radius:50%;background:var(--ink)}
  .brand-block{text-align:left}
  .brand-name{font-size:110px;font-weight:400;line-height:1;letter-spacing:1px}
  .brand-tagline{font-family:"Open Sans",sans-serif;font-weight:600;font-size:28px;color:var(--ink-soft);margin-top:4px}
  .product{position:absolute;left:0;right:0;top:285px}
  .product-name{font-size:100px;font-weight:400;line-height:.9}
  .product-blend{font-size:36px;font-weight:400;line-height:1.2}
  .product-origin{font-size:36px;font-weight:400;line-height:1.2}
  .product-description{font-family:"Open Sans",sans-serif;font-size:22px;font-weight:400;color:var(--ink-soft);margin-top:22px}
  .contact{
    position:absolute;left:200px;right:200px;top:548px;
    font-family:"Open Sans",sans-serif;font-weight:600;font-size:19px;
    color:var(--ink-soft);line-height:1.6;
  }
</style>
</head>
<body>
<main class="canvas">
  <section class="label">
    <svg class="frame" width="1000" height="683" viewBox="0 0 1000 683" aria-hidden="true">
      <path d="M150 62 Q500 22 850 62" fill="none" stroke="var(--ink)" stroke-width="4"/>
      <path d="M150 621 Q500 661 850 621" fill="none" stroke="var(--ink)" stroke-width="4"/>
      <path d="M36 150 Q26 341 36 533" fill="none" stroke="var(--ink)" stroke-width="4"/>
      <path d="M964 150 Q974 341 964 533" fill="none" stroke="var(--ink)" stroke-width="4"/>
    </svg>
    <div class="corner tl" role="img" aria-label="Ornement floral en volutes, coin supérieur gauche"></div>
    <div class="corner tr" role="img" aria-label="Ornement floral en volutes, coin supérieur droit"></div>
    <div class="corner bl" role="img" aria-label="Ornement floral en volutes, coin inférieur gauche"></div>
    <div class="corner br" role="img" aria-label="Ornement floral en volutes, coin inférieur droit"></div>
    <div class="sprig" role="img" aria-label="Branche de caféier avec feuilles vertes et cerises rouges"></div>

    <header class="brand">
      <span class="brand-dot"></span>
      <div class="brand-block">
        <div class="brand-name">SirKettle</div>
        <div class="brand-tagline">Artisan Torréfacteur</div>
      </div>
    </header>

    <div class="product">
      <h1 class="product-name">No5 de SirKettle</h1>
      <p class="product-blend">100% Arabica</p>
      <p class="product-origin">(Brésil, Congo, Ethiopie)</p>
      <p class="product-description">Description placed here</p>
    </div>

    <footer class="contact">
      <p>14 rue des Tilleuls 78000 Versailles &nbsp;|&nbsp; Tel. +33 1 45 20 71 38</p>
      <p>grains-du-matin.fr</p>
    </footer>
  </section>
</main>
</body>
</html>
```